Tallwick Home Services Web Site

Design Web site with 3-4 pages: Home, About Us, Services and Order form / Schedule Appointment (which will likely be link to Method App and Quickbooks integration.)
Services include: Dryer Vent Cleaning, AC Cleaning, Difficult-to-Reach Light Bulb replacement, Wood Repair and Home Maintenance Plans including Fire Safety Checks and Filter Replacement.

Target Market(s)

Luxury Home Owners, Professionals (Dr's/lawyers) and Seniors

Industry/Entity Type

Home Maintenance

Coding

Coded - Design and coding required

Requirements
Must have
• Tagline - Where Home Maintenance is Elementary

```html
<!DOCTYPE html>
<html lang="en">
<head>
<meta charset="utf-8">
<title>Tallwick Home Services</title>
<link href="https://fonts.googleapis.com/css2?family=Outfit:wght@400;500;600;700&family=Inter:wght@400;500;600&display=swap" rel="stylesheet">
<style>
:root{
  --grey:#66666e;
  --grey-dark:#55555c;
  --yellow:#e1a823;
  --ink:#1f1f22;
  --muted:#6b6b72;
  --circle:#f1f1f2;
  --white:#ffffff;
}
*{box-sizing:border-box;margin:0;padding:0}
html,body{width:1200px;height:3858px;overflow:hidden;background:var(--white)}
body{font-family:"Inter",sans-serif;color:var(--ink)}
.page{position:relative;width:1200px;height:3858px;overflow:hidden}
.abs{position:absolute}
.bg-svg{position:absolute;left:0;top:0}
h1,h2,h3{font-family:"Outfit",sans-serif}

.btn{position:absolute;display:flex;align-items:center;justify-content:center;gap:10px;background:var(--grey);color:var(--white);font-family:"Outfit",sans-serif;font-weight:500;font-size:15px;border-radius:3px;text-decoration:none;white-space:nowrap}
.btn .dot{width:20px;height:20px;border-radius:50%;background:var(--yellow);display:inline-flex;align-items:center;justify-content:center}

.brand{position:absolute;display:flex;align-items:center;gap:10px}
.brand .mark{width:34px;height:34px;border-radius:50%;background:var(--yellow)}
.brand .name{font-family:"Outfit",sans-serif;font-weight:600;font-size:22px;line-height:1.1;color:var(--yellow)}
.nav{position:absolute;left:458px;top:26px;display:flex;gap:28px;font-family:"Outfit",sans-serif;font-size:17px;font-weight:500;color:var(--ink)}
.nav a{color:inherit;text-decoration:none;position:relative}
.nav a.active{color:var(--yellow)}
.nav a.active::before{content:"";position:absolute;left:0;right:0;top:-26px;height:3px;background:var(--yellow)}

.hero-photo{position:absolute;left:0;top:0;width:1200px;height:790px;background:linear-gradient(120deg,#eceef0 0%,#d9dbde 40%,#b8c3d8 60%,#f2f2f2 100%)}
.hero-card{position:absolute;left:622px;top:145px;width:444px;height:444px;border-radius:50%;background:var(--white);text-align:center;padding-top:82px}
.pill{display:inline-block;background:var(--yellow);color:var(--ink);font-family:"Outfit",sans-serif;font-size:16px;font-weight:500;padding:5px 18px;border-radius:20px}
.hero-card h1{font-size:60px;font-weight:600;line-height:1.08;margin-top:10px}
.hero-card .tagline{font-size:16px;color:var(--muted);margin-top:14px;line-height:1.4}
.slider-dot{position:absolute;width:38px;height:38px;border-radius:50%;background:var(--white);box-shadow:0 2px 6px rgba(0,0,0,.2);display:flex;align-items:center;justify-content:center}

.stat{position:absolute;top:860px;width:211px;height:187px;background:var(--white);border-radius:8px;text-align:center}
.stat .ring{position:absolute;left:50%;top:30px;width:64px;height:64px;margin-left:-32px;border-radius:50%;background:var(--circle)}
.stat .num{position:absolute;left:0;right:0;top:42px;font-family:"Outfit",sans-serif;font-size:44px;font-weight:500;color:var(--yellow);line-height:1}
.stat .lbl{position:absolute;left:0;right:0;top:108px;font-family:"Outfit",sans-serif;font-size:21px;line-height:28px;color:var(--ink)}

.about-visual{position:absolute;left:142px;top:1250px;width:430px;height:458px;border-radius:0 0 215px 215px;background:linear-gradient(180deg,#ffffff 0%,#f5e4b8 35%,#c9cbd0 60%,#8f949c 100%)}
.eyebrow{font-family:"Outfit",sans-serif;font-size:16px;font-weight:500;color:var(--yellow);letter-spacing:.3px}
.rule{width:92px;height:3px;background:var(--yellow)}
.about-text{position:absolute;left:617px;top:1372px;width:440px;font-size:13.2px;line-height:24px;color:var(--muted);text-align:justify}

.services-bg{position:absolute;left:0;top:1812px;width:1200px;height:623px;background:linear-gradient(110deg,#ececee 0%,#f7f7f8 45%,#efeff1 100%)}
.section-title{position:absolute;left:0;width:1200px;text-align:center;font-size:42px;font-weight:600}
.service{position:absolute;top:1964px;width:214px;height:378px;background:var(--white);border-radius:8px;box-shadow:0 3px 12px rgba(0,0,0,.08);text-align:center}
.service.is-active{border:2px solid var(--yellow)}
.service .thumb{position:absolute;left:10px;top:8px;right:10px;height:176px;border-radius:6px}
.service h3{position:absolute;left:0;right:0;top:200px;font-size:21px;font-weight:500;line-height:1.35}
.service p{position:absolute;left:10px;right:10px;top:264px;font-size:13px;line-height:20px;color:var(--muted)}
.service .more{position:absolute;left:0;right:0;top:338px;font-family:"Outfit",sans-serif;font-size:15px;font-weight:600;color:var(--yellow)}
.service.is-active .more{text-decoration:underline}

.cta-title{position:absolute;left:143px;top:2500px;font-size:40px;font-weight:600;line-height:1.15;color:var(--white)}

.field{position:absolute;border:1px solid #b9b9be;border-radius:3px;background:rgba(255,255,255,.9);font-size:13px;color:var(--ink);padding-left:22px}
.field.line{height:59px;line-height:59px;top:2942px}
.world{position:absolute;left:300px;top:2870px;width:640px;height:400px;background:radial-gradient(ellipse at center,rgba(200,200,205,.35),rgba(255,255,255,0) 70%)}

.foot-head{position:absolute;font-family:"Outfit",sans-serif;font-weight:600;font-size:20px;color:var(--white);line-height:1.45}
.foot-list{position:absolute;list-style:none;font-size:14px;color:var(--white)}
.foot-list li{height:32px;display:flex;align-items:center;gap:12px}
.foot-list li::before{content:"»";color:var(--yellow);font-size:16px}
.info{position:absolute;left:503px;display:flex;gap:22px;color:var(--white)}
.info b{font-family:"Outfit",sans-serif;font-size:15px;font-weight:600;display:block}
.info span{font-size:12px}
.social{position:absolute;top:3662px;width:28px;height:28px;border-radius:50%;background:var(--grey-dark)}
.copyright{position:absolute;left:0;width:1200px;top:3808px;text-align:center;font-size:14px;color:var(--white)}
</style>
</head>
<body>
<div class="page">

  <div class="hero-photo" role="img" aria-label="Technician in a blue cap servicing a wall-mounted air conditioner"></div>
  <svg class="bg-svg" width="1200" height="1830" viewBox="0 0 1200 1830">
    <path d="M0,655 Q560,920 1200,535 L1200,1830 L0,1830 Z" fill="var(--yellow)"/>
    <path d="M0,675 Q560,930 1200,560 L1200,1830 L0,1830 Z" fill="var(--grey)"/>
    <path d="M0,1348 Q600,1060 1200,1280 L1200,1830 L0,1830 Z" fill="var(--yellow)"/>
    <path d="M0,1348 Q600,1085 1200,1290 L1200,1830 L0,1830 Z" fill="var(--white)"/>
    <path d="M722,158 A240,240 0 0 1 1010,515" fill="none" stroke="var(--yellow)" stroke-width="16"/>
    <path d="M640,470 A230,230 0 0 0 720,570" fill="none" stroke="var(--yellow)" stroke-width="14"/>
  </svg>

  <div class="brand" style="left:128px;top:64px">
    <span class="mark"></span>
    <span class="name">Tallwick<br>Home Services</span>
  </div>
  <nav class="nav">
    <a class="active" href="#">Home</a>
    <a href="#">About Us</a>
    <a href="#">Services</a>
    <a href="#">Contact</a>
  </nav>
  <a class="btn" href="#" style="left:829px;top:17px;width:224px;height:43px">Schedule Appointment <span class="dot"><svg width="8" height="10" viewBox="0 0 8 10"><path d="M2 1l4 4-4 4" stroke="#55555c" stroke-width="2" fill="none"/></svg></span></a>

  <div class="hero-card">
    <span class="pill">Welcome To</span>
    <h1>Tallwick<br>Homes</h1>
    <p class="tagline">Where Home Maintenance<br>is Elementary</p>
  </div>
  <a class="btn" href="#" style="left:770px;top:468px;width:145px;height:42px">Get Started <span class="dot"><svg width="8" height="10" viewBox="0 0 8 10"><path d="M2 1l4 4-4 4" stroke="#55555c" stroke-width="2" fill="none"/></svg></span></a>
  <div class="slider-dot" style="left:557px;top:646px"><svg width="10" height="14" viewBox="0 0 10 14"><path d="M7 2L2 7l5 5" stroke="#222" stroke-width="2" fill="none"/></svg></div>
  <div class="slider-dot" style="left:604px;top:646px"><svg width="10" height="14" viewBox="0 0 10 14"><path d="M3 2l5 5-5 5" stroke="#222" stroke-width="2" fill="none"/></svg></div>

  <div class="stat" style="left:144px"><span class="ring"></span><div class="num">10k+</div><div class="lbl">Project<br>Completion</div></div>
  <div class="stat" style="left:378px"><span class="ring"></span><div class="num">200+</div><div class="lbl">Experienced<br>Engineers</div></div>
  <div class="stat" style="left:611px"><span class="ring"></span><div class="num">11+</div><div class="lbl">Years of<br>Experience</div></div>
  <div class="stat" style="left:845px"><span class="ring"></span><div class="num">100%</div><div class="lbl">Customer<br>Satisfaction</div></div>

  <div class="about-visual" role="img" aria-label="Technician repairing an air conditioning unit inside a round frame"></div>
  <div class="eyebrow abs" style="left:613px;top:1263px">ABOUT US</div>
  <h2 class="abs" style="left:613px;top:1285px;font-size:42px;font-weight:600">Tallwick Homes</h2>
  <div class="rule abs" style="left:613px;top:1352px"></div>
  <p class="about-text">Lorem ipsum dolor sit amet, consectetur adipiscing elit, sed do eiusmod tempor incididunt ut labore et dolore magna aliqua. Ut enim ad minim veniam, quis nostrud exercitation ullamco laboris nisi ut aliquip ex ea commodo consequat. Duis aute irure dolor in reprehenderit in voluptate velit esse cillum dolore eu fugiat nulla pariatur. Excepteur sint occaecat cupidatat non proident, sunt in culpa qui officia deserunt mollit anim id est laborum. Lorem ipsum dolor sit amet, consectetur adipiscing elit, sed do eiusmod tempor incididunt ut labore et dolore magna aliqua. Ut enim ad minim veniam, quis nostrud exercitation ullamco laboris nisi ut aliquip ex ea commodo consequat. Duis aute irure dolor in reprehenderit in voluptate velit esse cillum dolore eu fugiat nulla pariatur.</p>
  <a class="btn" href="#" style="left:617px;top:1673px;width:183px;height:42px">View Our Services <span class="dot"><svg width="8" height="10" viewBox="0 0 8 10"><path d="M2 1l4 4-4 4" stroke="#55555c" stroke-width="2" fill="none"/></svg></span></a>

  <div class="services-bg"></div>
  <h2 class="section-title" style="top:1872px">Our Services</h2>
  <div class="rule abs" style="left:554px;top:1934px"></div>
  <div class="slider-dot" style="left:53px;top:2146px"><svg width="10" height="14" viewBox="0 0 10 14"><path d="M7 2L2 7l5 5" stroke="#222" stroke-width="2" fill="none"/></svg></div>
  <div class="slider-dot" style="left:1109px;top:2146px"><svg width="10" height="14" viewBox="0 0 10 14"><path d="M3 2l5 5-5 5" stroke="#222" stroke-width="2" fill="none"/></svg></div>

  <div class="service" style="left:144px">
    <div class="thumb" role="img" aria-label="Technician cleaning a dryer vent with an orange vacuum" style="background:linear-gradient(135deg,#e6e2da,#c9a184 55%,#8b8f93)"></div>
    <h3>Dryer<br>Vent Cleaning</h3>
    <p>Lorem ipsum dolor sit am et, consectetur adipis cing sed do eiusmod</p>
    <div class="more">Read More</div>
  </div>
  <div class="service is-active" style="left:374px">
    <div class="thumb" role="img" aria-label="Technician cleaning a wall air conditioner" style="background:linear-gradient(135deg,#eeeeee,#9aa9c4 55%,#4b6aa5)"></div>
    <h3>AC<br>Cleaning</h3>
    <p>Lorem ipsum dolor sit am et, consectetur adipis cing sed do eiusmod</p>
    <div class="more">Read More</div>
  </div>
  <div class="service" style="left:608px">
    <div class="thumb" role="img" aria-label="Electrician replacing a ceiling light bulb" style="background:linear-gradient(135deg,#f2f2f2,#c5c9d2 55%,#6e7fa6)"></div>
    <h3>Light Bulb<br>Replacement</h3>
    <p>Lorem ipsum dolor sit am et, consectetur adipis cing sed do eiusmod</p>
    <div class="more">Read More</div>
  </div>
  <div class="service" style="left:842px">
    <div class="thumb" role="img" aria-label="Worker repairing a wooden table" style="background:linear-gradient(135deg,#d9cfc2,#a0846a 55%,#4f5b6e)"></div>
    <h3>Wood<br>Repair</h3>
    <p>Lorem ipsum dolor sit am et, consectetur adipis cing sed do eiusmod</p>
    <div class="more">Read More</div>
  </div>

  <svg class="bg-svg" style="top:2435px" width="1200" height="342" viewBox="0 0 1200 342">
    <rect width="1200" height="342" fill="var(--yellow)"/>
    <polygon points="824,0 1200,0 1200,342 716,342" fill="var(--white)"/>
    <polygon points="842,0 1200,0 1200,342 734,342" fill="#c9ced6"/>
  </svg>
  <div class="abs" role="img" aria-label="Technician carrying a toolbox toward an air conditioner in a bright room" style="left:734px;top:2435px;width:466px;height:342px;clip-path:polygon(108px 0,466px 0,466px 342px,0 342px);background:linear-gradient(120deg,#e4e6ea 0%,#cfd5df 40%,#3f64b3 60%,#b99d74 85%,#ecedef 100%)"></div>
  <h2 class="cta-title">Your Home.<br>Solved with Care.</h2>
  <div class="abs" style="left:143px;top:2612px;width:54px;height:3px;background:var(--white)"></div>
  <a class="btn" href="#" style="left:148px;top:2639px;width:243px;height:42px">Request Free Consultation <span class="dot"><svg width="8" height="10" viewBox="0 0 8 10"><path d="M2 1l4 4-4 4" stroke="#55555c" stroke-width="2" fill="none"/></svg></span></a>

  <div class="world" role="img" aria-label="Faint dotted world map"></div>
  <h2 class="section-title" style="top:2830px">Get In Touch</h2>
  <div class="rule abs" style="left:554px;top:2897px"></div>
  <div class="field line" style="left:142px;width:294px">Name</div>
  <div class="field line" style="left:452px;width:294px">Email</div>
  <div class="field line" style="left:764px;width:292px">Phone</div>
  <div class="field" style="left:142px;top:3021px;width:914px;height:164px;padding-top:14px">Message</div>
  <a class="btn" href="#" style="left:527px;top:3203px;width:144px;height:40px">Submit Now <span class="dot"><svg width="8" height="10" viewBox="0 0 8 10"><path d="M2 1l4 4-4 4" stroke="#55555c" stroke-width="2" fill="none"/></svg></span></a>

  <svg class="bg-svg" style="top:3310px" width="1200" height="548" viewBox="0 0 1200 548">
    <path d="M0,165 Q520,-30 1200,240 L1200,548 L0,548 Z" fill="var(--yellow)"/>
    <path d="M0,180 Q520,-10 1200,262 L1200,548 L0,548 Z" fill="var(--grey)"/>
  </svg>
  <div class="brand" style="left:226px;top:3428px">
    <span class="mark"></span>
    <span class="name" style="color:var(--white)">Tallwick<br>Home Services</span>
  </div>

  <div class="foot-head" style="left:144px;top:3528px">SUBSCRIBE TO<br>OUR NEWSLETTER</div>
  <div class="abs" style="left:144px;top:3602px;width:271px;height:40px;background:var(--grey-dark);border-radius:2px;color:#e6e6e6;font-size:12px;line-height:40px;padding-left:16px">Email address
    <svg class="abs" style="right:10px;top:13px" width="15" height="14" viewBox="0 0 15 14"><path d="M1 7L14 1 10 13 7 8z" fill="var(--yellow)"/></svg>
  </div>
  <div class="social" style="left:144px"></div>
  <div class="social" style="left:176px;background:var(--yellow)"></div>
  <div class="social" style="left:208px"></div>

  <div class="foot-head" style="left:503px;top:3528px">CONTACT INFO</div>
  <div class="info" style="top:3585px">
    <svg width="14" height="18" viewBox="0 0 14 18"><path d="M7 0a7 7 0 0 0-7 7c0 5 7 11 7 11s7-6 7-11a7 7 0 0 0-7-7zm0 10a3 3 0 1 1 0-6 3 3 0 0 1 0 6z" fill="var(--yellow)"/></svg>
    <div><b>Address</b><span>Lorem ipsum dolor sit amet</span></div>
  </div>
  <div class="info" style="top:3640px">
    <svg width="18" height="14" viewBox="0 0 18 14"><rect width="18" height="14" rx="2" fill="var(--yellow)"/><path d="M1 2l8 6 8-6" stroke="#66666e" stroke-width="1.5" fill="none"/></svg>
    <div><b>Email</b><span>info@companyname.com</span></div>
  </div>
  <div class="info" style="top:3696px">
    <svg width="16" height="16" viewBox="0 0 16 16"><path d="M3 1l3 3-2 2c1 2 3 4 5 5l2-2 3 3-2 3C7 15 1 9 1 3z" fill="var(--yellow)"/></svg>
    <div><b>Phone</b><span>+1 888 888 8888</span></div>
  </div>

  <div class="foot-head" style="left:765px;top:3528px">QUICK LINKS</div>
  <ul class="foot-list" style="left:765px;top:3579px"><li>Home</li><li>About</li><li>Services</li><li>Contact</li></ul>
  <ul class="foot-list" style="left:900px;top:3579px"><li>Terms and Condition</li><li>Privacy policy</li><li>Help</li><li>Support</li></ul>

  <div class="copyright">© Copyrights 2025 | All Rights Reserved</div>
</div>
</body>
</html>
```